Dura Pike Poster- Graphic Design for Advertising Employment Opportunities.

DURA PIKE is a used motor oil collection and processing company.

We want to animate the truck and use it to create a graphic design used for advertising employment opportunities.

We need open areas to overlay custom wording.

This poster will be posted in truck stops, used at job fairs and advertised in newspapers.

Target Market(s)

Job seekers, skilled workers, truck drivers.

Industry/Entity Type

Recycling

Font styles to use
Serif
Sans Serif

Requirements
Must have
• Grayscale coloring preferred. Masculine. Complementing colors to the logo.
• Eye catching. Professional.
• MUST have open areas for customize-able wording.

```html
<!DOCTYPE html>
<html lang="en">
<head>
<meta charset="utf-8">
<title>Dura Pike — Flyer Colour and Grayscale Versions</title>
<link rel="stylesheet" href="https://fonts.googleapis.com/css2?family=Josefin+Sans:wght@400;600;700&family=Montserrat:wght@400;500;600&display=swap">
<style>
  :root {
    --board: #fbf0d6;
    --dark-top: #15162a;
    --panel-light: #d4d4d6;
    --panel-mid: #b9b9bc;
    --logo-gray: #7b7b80;
    --orange: #ef5a24;
    --navy: #1c2045;
    --black: #141414;
    --text: #2a2a2a;
  }
  html, body {
    margin: 0; padding: 0;
    width: 1200px; height: 893px;
    overflow: hidden;
    background: var(--board);
  }
  .board { position: relative; width: 1200px; height: 893px; }

  .flyer {
    position: absolute; top: 11px;
    width: 648px; height: 974px;
    transform: scale(0.8929);
    transform-origin: 0 0;
    overflow: hidden;
    box-shadow: 0 2px 6px rgba(0,0,0,.35);
    font-family: "Montserrat", Arial, sans-serif;
    color: var(--text);
  }
  .flyer--color { left: 12px; --top: var(--dark-top); --accent: var(--orange); --ink: var(--navy); --band: var(--orange); --band-text: var(--navy); --truck-a: #55565c; --truck-b: var(--orange); }
  .flyer--mono  { left: 609px; --top: #1c1c1c; --accent: var(--black); --ink: var(--black); --band: var(--black); --band-text: #ffffff; --truck-a: #5c5c5c; --truck-b: #a9a9a9; }

  .flyer__backdrop { position: absolute; inset: 0; }

  .flyer__mark {
    position: absolute; left: 284px; top: 52px;
    width: 108px; height: 108px; border-radius: 50%;
    background: var(--logo-gray);
  }
  .flyer__brand {
    position: absolute; left: 0; right: 0; top: 194px;
    text-align: center;
    font-family: "Josefin Sans", Arial, sans-serif;
    font-weight: 600; font-size: 62px; letter-spacing: 1px;
    color: var(--logo-gray);
  }

  .flyer__truck {
    position: absolute; left: 22px; top: 262px;
    width: 612px; height: 322px;
    clip-path: polygon(0 28%, 48% 0, 100% 18%, 100% 94%, 86% 100%, 62% 100%, 60% 82%, 0 72%);
    background: linear-gradient(100deg, var(--truck-a) 0%, var(--truck-a) 48%, var(--truck-b) 56%, var(--truck-b) 100%);
  }

  .flyer__headline {
    position: absolute; left: 50px; top: 574px; margin: 0;
    font-family: "Josefin Sans", Arial, sans-serif;
    color: var(--ink); line-height: 38px;
  }
  .flyer__headline strong { display: block; font-weight: 700; font-size: 42px; }
  .flyer__headline span { display: block; font-weight: 400; font-size: 37px; }

  .flyer__body {
    position: absolute; left: 52px; top: 660px; width: 378px;
    font-size: 10.8px; line-height: 13.1px; text-align: justify;
  }
  .flyer__body p { margin: 0 0 13px; }

  .flyer__divider {
    position: absolute; left: 455px; top: 668px;
    width: 2px; height: 212px; background: var(--ink);
  }

  .contact {
    position: absolute; left: 476px; top: 726px; width: 170px;
    font-size: 11px; color: var(--ink);
  }
  .contact__title {
    margin: 0 0 8px; font-family: "Josefin Sans", Arial, sans-serif;
    font-weight: 700; font-size: 12px;
  }
  .contact__list { list-style: none; margin: 0; padding: 0; }
  .contact__item { display: flex; align-items: flex-start; gap: 7px; margin-bottom: 8px; line-height: 11px; }
  .contact__item svg { flex: none; width: 11px; height: 11px; }
  .contact__follow { margin: 16px 0 10px; }
  .social { display: flex; align-items: center; gap: 7px; font-weight: 600; font-size: 13px; }
  .social__mark { width: 18px; height: 18px; background: var(--accent); }

  .band {
    position: absolute; left: 0; right: 0; top: 920px;
    text-align: center; color: var(--band-text);
  }
  .band__title { margin: 4px 0 3px; font-family: "Josefin Sans", Arial, sans-serif; font-size: 16px; font-weight: 400; }
  .band__text { margin: 0 auto; width: 470px; font-size: 11px; line-height: 13px; }
</style>
</head>
<body>
<main class="board">

  <article class="flyer flyer--color">
    <svg class="flyer__backdrop" viewBox="0 0 648 974" preserveAspectRatio="none" aria-hidden="true">
      <rect width="648" height="974" fill="var(--top)"/>
      <path d="M0 462 Q300 452 648 560 L648 974 L0 974Z" fill="var(--panel-light)"/>
      <path d="M280 510 Q520 540 648 620 L648 700 Q520 580 280 510Z" fill="var(--panel-mid)"/>
      <path d="M420 900 Q560 820 648 700 L648 760 Q560 860 440 905Z" fill="#e6e6e8"/>
      <path d="M0 893 Q330 880 648 905 L648 912 L0 912Z" fill="#4a4a4e"/>
      <path d="M0 902 Q330 892 648 915 L648 974 L0 974Z" fill="var(--band)"/>
    </svg>
    <div class="flyer__mark"></div>
    <div class="flyer__brand">DURA PIKE</div>
    <div class="flyer__truck" role="img" aria-label="Illustration of a tanker truck with an orange cab and gray tank trailers"></div>
    <h1 class="flyer__headline"><strong>DURA PIKE</strong><span>LOREM IPSUM</span></h1>
    <div class="flyer__body">
      <p>Lorem ipsum dolor sit amet, consectetur adipisicing elit, sed do eiusmod tempor incididunt ut labore et dolore magna aliqua. Ut enim ad minim veniam, quis nostrud exercitation ullamco laboris nisi ut aliquip ex ea commodo consequat. Duis aute irure dolor in reprehenderit in voluptate velit esse cillum dolore eu fugiat nulla pariatur. Excepteur sint occaecat cupidatat non proident, sunt in culpa qui officia deserunt mollit anim id est laborum.</p>
      <p>Sed ut perspiciatis unde omnis iste natus error sit voluptatem accusantium doloremque laudantium, totam rem aperiam, eaque ipsa quae ab illo inventore veritatis et quasi architecto beatae vitae dicta sunt explicabo. Nemo enim ipsam voluptatem quia voluptas sit aspernatur aut odit aut fugit, sed quia consequuntur magni dolores eos qui ratione voluptatem sequi nesciunt. Neque porro quisquam est, qui dolorem ipsum quia dolor sit amet, consectetur, adipisci velit, sed quia non numquam eius modi tempora incidunt ut labore et dolore magnam aliquam quaerat voluptatem.</p>
    </div>
    <div class="flyer__divider"></div>
    <section class="contact">
      <h2 class="contact__title">CONTACT US ON:</h2>
      <ul class="contact__list">
        <li class="contact__item"><svg viewBox="0 0 12 12"><path d="M2 1 L4.5 1 L5.3 3.6 L4 4.6 Q5 7 7.4 8 L8.4 6.7 L11 7.5 L11 10 Q6 11 2.5 7.5 Q0.6 4.8 2 1Z" fill="var(--accent)"/></svg>123 456 789</li>
        <li class="contact__item"><svg viewBox="0 0 12 12"><rect x="1" y="2.5" width="10" height="7" fill="none" stroke="var(--accent)" stroke-width="1.2"/><path d="M1 2.5 L6 6.5 L11 2.5" fill="none" stroke="var(--accent)" stroke-width="1.2"/></svg>hello@durapike.com</li>
        <li class="contact__item"><svg viewBox="0 0 12 12"><circle cx="6" cy="6" r="5" fill="none" stroke="var(--ink)" stroke-width="1"/><ellipse cx="6" cy="6" rx="2.2" ry="5" fill="none" stroke="var(--ink)" stroke-width="1"/><path d="M1 6 H11" stroke="var(--ink)" stroke-width="1"/></svg>www.durapike.com</li>
        <li class="contact__item"><svg viewBox="0 0 12 12"><path d="M6 11 Q2 6.5 2 4.5 A4 4 0 0 1 10 4.5 Q10 6.5 6 11Z" fill="var(--accent)"/><circle cx="6" cy="4.5" r="1.4" fill="#fff"/></svg><span>123 Lorem ipsum,<br>Dolor sit amet,<br>Consectetur</span></li>
      </ul>
      <h2 class="contact__title contact__follow">FOLLOW AND LIKE US ON:</h2>
      <div class="social"><span class="social__mark"></span>@durapike</div>
    </section>
    <footer class="band">
      <h3 class="band__title">LOREM IPSUM</h3>
      <p class="band__text">Lorem ipsum dolor sit amet, consectetur adipisicing elit, sed do eiusmod tempor incididunt ut labore et dolore magna aliqua.</p>
    </footer>
  </article>

  <article class="flyer flyer--mono">
    <svg class="flyer__backdrop" viewBox="0 0 648 974" preserveAspectRatio="none" aria-hidden="true">
      <rect width="648" height="974" fill="var(--top)"/>
      <path d="M0 462 Q300 452 648 560 L648 974 L0 974Z" fill="var(--panel-light)"/>
      <path d="M280 510 Q520 540 648 620 L648 700 Q520 580 280 510Z" fill="var(--panel-mid)"/>
      <path d="M420 900 Q560 820 648 700 L648 760 Q560 860 440 905Z" fill="#e6e6e8"/>
      <path d="M0 893 Q330 880 648 905 L648 912 L0 912Z" fill="#4a4a4e"/>
      <path d="M0 902 Q330 892 648 915 L648 974 L0 974Z" fill="var(--band)"/>
    </svg>
    <div class="flyer__mark"></div>
    <div class="flyer__brand">DURA PIKE</div>
    <div class="flyer__truck" role="img" aria-label="Illustration of a tanker truck in shades of gray"></div>
    <h1 class="flyer__headline"><strong>DURA PIKE</strong><span>LOREM IPSUM</span></h1>
    <div class="flyer__body">
      <p>Lorem ipsum dolor sit amet, consectetur adipisicing elit, sed do eiusmod tempor incididunt ut labore et dolore magna aliqua. Ut enim ad minim veniam, quis nostrud exercitation ullamco laboris nisi ut aliquip ex ea commodo consequat. Duis aute irure dolor in reprehenderit in voluptate velit esse cillum dolore eu fugiat nulla pariatur. Excepteur sint occaecat cupidatat non proident, sunt in culpa qui officia deserunt mollit anim id est laborum.</p>
      <p>Sed ut perspiciatis unde omnis iste natus error sit voluptatem accusantium doloremque laudantium, totam rem aperiam, eaque ipsa quae ab illo inventore veritatis et quasi architecto beatae vitae dicta sunt explicabo. Nemo enim ipsam voluptatem quia voluptas sit aspernatur aut odit aut fugit, sed quia consequuntur magni dolores eos qui ratione voluptatem sequi nesciunt. Neque porro quisquam est, qui dolorem ipsum quia dolor sit amet, consectetur, adipisci velit, sed quia non numquam eius modi tempora incidunt ut labore et dolore magnam aliquam quaerat voluptatem.</p>
    </div>
    <div class="flyer__divider"></div>
    <section class="contact">
      <h2 class="contact__title">CONTACT US ON:</h2>
      <ul class="contact__list">
        <li class="contact__item"><svg viewBox="0 0 12 12"><path d="M2 1 L4.5 1 L5.3 3.6 L4 4.6 Q5 7 7.4 8 L8.4 6.7 L11 7.5 L11 10 Q6 11 2.5 7.5 Q0.6 4.8 2 1Z" fill="var(--accent)"/></svg>123 456 789</li>
        <li class="contact__item"><svg viewBox="0 0 12 12"><rect x="1" y="2.5" width="10" height="7" fill="none" stroke="var(--accent)" stroke-width="1.2"/><path d="M1 2.5 L6 6.5 L11 2.5" fill="none" stroke="var(--accent)" stroke-width="1.2"/></svg>hello@durapike.com</li>
        <li class="contact__item"><svg viewBox="0 0 12 12"><circle cx="6" cy="6" r="5" fill="none" stroke="var(--ink)" stroke-width="1"/><ellipse cx="6" cy="6" rx="2.2" ry="5" fill="none" stroke="var(--ink)" stroke-width="1"/><path d="M1 6 H11" stroke="var(--ink)" stroke-width="1"/></svg>www.durapike.com</li>
        <li class="contact__item"><svg viewBox="0 0 12 12"><path d="M6 11 Q2 6.5 2 4.5 A4 4 0 0 1 10 4.5 Q10 6.5 6 11Z" fill="var(--accent)"/><circle cx="6" cy="4.5" r="1.4" fill="#fff"/></svg><span>123 Lorem ipsum,<br>Dolor sit amet,<br>Consectetur</span></li>
      </ul>
      <h2 class="contact__title contact__follow">FOLLOW AND LIKE US ON:</h2>
      <div class="social"><span class="social__mark"></span>@durapike</div>
    </section>
    <footer class="band">
      <h3 class="band__title">LOREM IPSUM</h3>
      <p class="band__text">Lorem ipsum dolor sit amet, consectetur adipisicing elit, sed do eiusmod tempor incididunt ut labore et dolore magna aliqua.</p>
    </footer>
  </article>

</main>
</body>
</html>
```